Market Research firm needs updated business cards with new logo

We need the logo to be included somewhere on the card (attached). We would also like the phrases "Independent, Objective, Comprehensive" and "Research You Can Trust" somewhere on the card. Front or back. Our colors are hex codes 6075a7, e48d25 and 5a5b5b. Though you are certainly not limited to those shades, whatever you produce should coordinate with them. I have also attached our favicon. Feel free to use it in your design, but please do not use it to replace the full logo.

Contact Information for Business Card

see project description

Font styles to use
Other font styles liked:
• Open Sans

Requirements
Must have
• the logo
• We use Open Sans font

```html
<!DOCTYPE html>
<html lang="en">
<head>
<meta charset="utf-8">
<title>Norvale Research — Business Card</title>
<link href="https://fonts.googleapis.com/css2?family=Open+Sans:wght@400;600;700&display=swap" rel="stylesheet">
<style>
  :root {
    --page: #ffffff;
    --card: #5a5b5b;
    --orange: #e48d25;
    --blue: #6075a7;
  }
  * { margin: 0; padding: 0; box-sizing: border-box; }
  html, body { width: 1200px; height: 1200px; overflow: hidden; background: var(--page); }
  body { position: relative; font-family: "Open Sans", Arial, sans-serif; }

  .card {
    position: absolute;
    left: 181px;
    width: 839px;
    height: 478px;
    background: var(--card);
    border-radius: 19px;
    overflow: hidden;
  }
  .card--front { top: 104px; }
  .card--back { top: 617px; }

  .accent-bar {
    position: absolute;
    top: 102px;
    height: 234px;
    background: var(--orange);
  }
  .accent-bar--left { left: 0; width: 27px; }
  .accent-bar--right { right: 0; width: 29px; }

  .wordmark {
    position: absolute;
    color: var(--orange);
    font-weight: 600;
    white-space: nowrap;
    letter-spacing: -0.5px;
  }
  .card--front .wordmark { left: 42px; top: 106px; font-size: 44px; line-height: 1; }

  .holder-name {
    position: absolute; left: 62px; top: 250px;
    color: var(--orange); font-weight: 700; font-size: 27px; line-height: 1;
  }
  .holder-title {
    position: absolute; left: 66px; top: 279px;
    color: var(--orange); font-size: 17px; line-height: 1;
  }

  .divider {
    position: absolute; left: 29px; right: 29px; top: 334px;
    border-top: 2px dotted var(--orange);
    opacity: 0.8;
  }

  .contact-list { position: absolute; left: 50px; top: 340px; list-style: none; }
  .contact-item {
    display: flex; align-items: center; height: 24px;
    color: var(--blue); font-size: 25px; margin-bottom: 19px;
  }
  .contact-item svg { width: 24px; height: 24px; margin-right: 15px; flex: none; }

  .location { position: absolute; left: 546px; top: 342px; display: flex; }
  .location svg { width: 24px; height: 32px; margin-right: 10px; flex: none; }
  .location-text { color: var(--blue); font-size: 19px; line-height: 28px; }

  .card--back .wordmark {
    left: 0; right: 0; top: 176px; text-align: center;
    font-size: 84px; line-height: 1;
  }
  .tagline {
    position: absolute; left: 95px; right: 95px; top: 304px;
    display: flex; justify-content: space-between;
    color: var(--orange); font-weight: 700; font-size: 18.5px; letter-spacing: 0.3px;
  }
</style>
</head>
<body>

  <section class="card card--front">
    <div class="accent-bar accent-bar--left"></div>
    <div class="accent-bar accent-bar--right"></div>

    <div class="wordmark">Norvale Research</div>

    <div class="holder-name">DANA MERCER</div>
    <div class="holder-title">Ceo/Owner</div>

    <div class="divider"></div>

    <ul class="contact-list">
      <li class="contact-item">
        <svg viewBox="0 0 24 24" aria-hidden="true">
          <circle cx="12" cy="12" r="12" fill="var(--orange)"/>
          <path d="M8 6.5c.6-.4 1.2-.3 1.5.3l1 1.8c.3.5.2 1-.2 1.3l-.8.6c.6 1.4 1.6 2.5 3 3.1l.6-.8c.3-.4.9-.5 1.3-.2l1.8 1c.6.3.7 1 .3 1.5l-.9 1c-.7.7-1.8.8-2.7.3-2.7-1.4-4.6-3.4-5.7-6.1-.4-.9-.2-2 .5-2.6z" fill="var(--card)"/>
        </svg>
        555-014-2286
      </li>
      <li class="contact-item">
        <svg viewBox="0 0 24 24" aria-hidden="true" fill="none" stroke="var(--orange)" stroke-width="1.6">
          <circle cx="12" cy="12" r="10"/>
          <ellipse cx="12" cy="12" rx="4.5" ry="10"/>
          <line x1="2" y1="12" x2="22" y2="12"/>
          <path d="M4 7h16M4 17h16"/>
        </svg>
        www.norvaleresearch.com
      </li>
      <li class="contact-item">
        <svg viewBox="0 0 24 24" aria-hidden="true">
          <rect x="1" y="5" width="22" height="14" fill="var(--orange)"/>
          <path d="M1 5l11 8 11-8M1 19l8-7M23 19l-8-7" fill="none" stroke="var(--card)" stroke-width="1.4"/>
        </svg>
        hello@norvaleresearch.com
      </li>
    </ul>

    <div class="location">
      <svg viewBox="0 0 24 32" aria-hidden="true">
        <path d="M12 1C6 1 1.5 5.5 1.5 11.2 1.5 18.5 12 31 12 31s10.5-12.5 10.5-19.8C22.5 5.5 18 1 12 1z" fill="var(--orange)"/>
        <circle cx="12" cy="11" r="4" fill="var(--card)"/>
      </svg>
      <div class="location-text">Your city, MO 00000<br>555-014-2286</div>
    </div>
  </section>

  <section class="card card--back">
    <div class="wordmark">Norvale Research</div>
    <div class="tagline">
      <span>INDEPENDENT</span>
      <span>COMPREHENSIVE</span>
      <span>RESEARCH YOU CAN TRUST</span>
    </div>
  </section>

</body>
</html>
```